Laser Tattoo Removal Business Cards

We are looking for a professional business card design for a laser tattoo removal business. Ideally looking for a black business card design. The name of the business is Palevane Tattoo Removal. We place our cards at local tattoo shops so we ideally are looking for something trendy/edgy to draw both male and female clientele in.

Target Market(s)

Male/Female ages 18-60

Contact Information for Business Card

black background ideally.. hoping to stay within greys, whites and black

Font styles to use
Serif
Sans Serif

Colors
121212
a9a9a9
5c5c5c
f5f5f5
ffffff
7f7f7f
606060
848484
9d9d9d

Requirements
Must have
• Employee Info:
• Melissa Thornbury
• Chief Executive Offer
• m: 919.537.2846
• w: 919.362.4178
• f: 919.685.3907
• mthornbury@palevanetattooremoval.example
• Address:
• 4615 Oakmere Pkwy, Suite 210
• Raleigh, NC 27654
• Website:
• www.palevanetattooremoval.example
Nice to have
• Myabe business name on back or logo on back and employee info on the front

```html
<!DOCTYPE html>
<html lang="en">
<head>
<meta charset="utf-8">
<title>Palevane Tattoo Removal – Business Cards</title>
<link rel="stylesheet" href="https://fonts.googleapis.com/css2?family=Roboto:wght@400;500&display=swap">
<style>
  :root {
    --ink: #121212;
    --paper: #f5f5f5;
    --white: #ffffff;
    --grey-dark: #5c5c5c;
    --grey-mid: #7f7f7f;
    --grey-light: #a9a9a9;
    --backdrop: #9d9d9d;
  }
  * { margin: 0; padding: 0; box-sizing: border-box; }
  html, body {
    width: 1105px; height: 1200px; overflow: hidden;
    background: var(--backdrop);
    font-family: "Roboto", Arial, sans-serif;
  }
  .canvas { position: relative; width: 1105px; height: 1200px; }

  .card { position: absolute; left: 182px; width: 746px; height: 427px; }
  .card-front { top: 119px; background: var(--paper); color: var(--ink); }
  .card-back { top: 637px; background: var(--ink); color: var(--white); }

  .wordmark {
    position: absolute; display: flex; flex-direction: column; align-items: center;
    font-weight: 500; text-transform: uppercase; line-height: 1;
  }
  .wordmark-name { display: block; letter-spacing: 0.04em; }
  .wordmark-tag { display: flex; align-items: center; letter-spacing: 0.12em; }
  .wordmark-tag::before, .wordmark-tag::after {
    content: ""; display: block; height: 1.5px; background: currentColor;
  }

  .card-front .wordmark { left: 20px; width: 318px; top: 154px; color: var(--ink); }
  .card-front .wordmark-name { font-size: 48px; }
  .card-front .wordmark-tag { font-size: 17px; margin-top: 74px; }
  .card-front .wordmark-tag::before { width: 16px; margin-right: 8px; }
  .card-front .wordmark-tag::after { width: 16px; margin-left: 6px; }

  .card-back .wordmark { left: 0; width: 746px; top: 128px; color: var(--white); }
  .card-back .wordmark-name { font-size: 58px; }
  .card-back .wordmark-tag { font-size: 22px; margin-top: 84px; }
  .card-back .wordmark-tag::before { width: 20px; margin-right: 10px; }
  .card-back .wordmark-tag::after { width: 20px; margin-left: 8px; }

  .divider {
    position: absolute; left: 350px; top: 102px; width: 1px; height: 269px;
    background: var(--grey-light);
  }

  .contact { position: absolute; left: 380px; top: 101px; }
  .contact-name { font-size: 22px; font-weight: 500; letter-spacing: 0.01em; text-transform: uppercase; color: var(--ink); }
  .contact-title { font-size: 16px; color: var(--grey-mid); margin-top: 2px; }
  .contact-address { font-size: 16px; line-height: 23px; color: var(--grey-dark); margin-top: 14px; }
  .contact-list { list-style: none; margin-top: 9px; }
  .contact-list li {
    display: flex; align-items: center; height: 23.5px;
    font-size: 16px; color: var(--grey-dark);
  }
  .contact-list li.email { font-size: 15px; }
  .contact-list svg { width: 14px; height: 14px; margin-right: 13px; flex: none; fill: var(--ink); }

  .back-web {
    position: absolute; left: 0; width: 746px; top: 363px; text-align: center;
    font-size: 16px; letter-spacing: 0.14em; color: var(--paper);
  }
</style>
</head>
<body>
<main class="canvas">
  <section class="card card-front" aria-label="Card front">
    <div class="wordmark">
      <span class="wordmark-name">Palevane</span>
      <span class="wordmark-tag">Tattoo Removal</span>
    </div>
    <div class="divider"></div>
    <div class="contact">
      <p class="contact-name">Melissa Thornbury</p>
      <p class="contact-title">Chief Executive Offer</p>
      <p class="contact-address">4615 Oakmere Pkwy, Suite 210<br>Raleigh, NC 27654</p>
      <ul class="contact-list">
        <li><svg viewBox="0 0 16 16" aria-label="Work phone"><path d="M3.6 1.2l2.3 2.6c.3.4.3.9 0 1.2L4.7 6.3c.9 2 2.9 4 5 5l1.3-1.2c.3-.3.8-.3 1.2 0l2.6 2.3c.4.3.4.9 0 1.3l-1.4 1.4c-.6.6-1.6.8-2.5.4C6.6 14 2 9.4.5 5.1.1 4.2.3 3.2.9 2.6L2.3 1.2c.4-.4 1-.4 1.3 0z"/></svg>919.362.4178</li>
        <li><svg viewBox="0 0 16 16" aria-label="Mobile phone"><path d="M4.5 0h7A1.5 1.5 0 0 1 13 1.5v13a1.5 1.5 0 0 1-1.5 1.5h-7A1.5 1.5 0 0 1 3 14.5v-13A1.5 1.5 0 0 1 4.5 0zM4.6 2v10.5h6.8V2zM8 13.3a.9.9 0 1 0 0 1.8.9.9 0 0 0 0-1.8z"/></svg>919.537.2846</li>
        <li><svg viewBox="0 0 16 16" aria-label="Fax"><path d="M4 0h8v4H4zM1.5 5h13A1.5 1.5 0 0 1 16 6.5V12h-3v4H3v-4H0V6.5A1.5 1.5 0 0 1 1.5 5zM4.5 10.5v4h7v-4zM13 6.5a.8.8 0 1 0 0 1.6.8.8 0 0 0 0-1.6z"/></svg>919.685.3907</li>
        <li class="email"><svg viewBox="0 0 16 16" aria-label="Email"><path d="M0 3h16v1.2L8 9 0 4.2zM0 5.8l8 4.8 8-4.8V13H0z"/></svg>mthornbury@palevanetattooremoval.example</li>
        <li><svg viewBox="0 0 16 16" aria-label="Website"><path d="M8 0a8 8 0 1 0 0 16A8 8 0 0 0 8 0zm-1 1.7v2.1L5 5.5 4 8l2 2v2.5l1 1.8A6.4 6.4 0 0 1 1.7 7.2l2 .3L5.2 5 4.5 3A6.4 6.4 0 0 1 7 1.7zm3.2.4A6.4 6.4 0 0 1 14.3 8l-1.8-1-2 .5-.6 2 1.5 1.5.1 2.2A6.4 6.4 0 0 1 10 14l.5-2.6-2-1.9.3-2 1.6-1.5L9 4.8z"/></svg>www.palevanetattooremoval.example</li>
      </ul>
    </div>
  </section>

  <section class="card card-back" aria-label="Card back">
    <div class="wordmark">
      <span class="wordmark-name">Palevane</span>
      <span class="wordmark-tag">Tattoo Removal</span>
    </div>
    <p class="back-web">www.palevanetattooremoval.example</p>
  </section>
</main>
</body>
</html>
```